Tollen Ridge Canvas Camps

I am Moving from nest QiV and Qelt to host my own website to create direct bookings. I haves booking platform, I just need a website to embed it into. I want a catchy website to attract potential guests to book at my accommodation located near morvane national park in Alberta, Canada.

Here is my nest QiV links:
https://www.nestqiv.ca/rooms/2048613927465105319?viralityEntryPoint=1&s=76

https://www.nestqiv.ca/rooms/2093547718260493127?viralityEntryPoint=1&s=76

https://www.nestqiv.ca/rooms/2184736590218374662?viralityEntryPoint=1&s=76

https://www.nestqiv.ca/rooms/2065128834710952483?viralityEntryPoint=1&s=76

https://www.nestqiv.ca/rooms/2317465098321857704?viralityEntryPoint=1&s=76

```html
<!DOCTYPE html>
<html lang="en">
<head>
<meta charset="UTF-8">
<title>Tollen Ridge Canvas Camps</title>
<link href="https://fonts.googleapis.com/css2?family=Lato:wght@400;700&family=Playfair+Display:wght@400;500&display=swap" rel="stylesheet">
<style>
:root{
  --cream:#f7f4ee;
  --ink:#2b2b2b;
  --muted:#555;
  --gold:#c8922f;
  --gold-dark:#a87621;
  --card:#ffffff;
  --night:#1c1c1c;
  --line:#e4ded3;
}
*{box-sizing:border-box;margin:0;padding:0}
html,body{width:1200px;height:4644px;overflow:hidden}
body{background:var(--cream);font-family:'Lato',sans-serif;color:var(--ink);position:relative}
.abs{position:absolute}
h1,h2,h3.serif{font-family:'Playfair Display',serif;font-weight:400}
.btn{display:inline-block;background:var(--gold);color:#fff;border-radius:22px;font-size:14px;font-weight:700;padding:11px 26px;text-decoration:none;box-shadow:0 3px 8px rgba(0,0,0,.15)}
.photo{border-radius:14px}

/* nav */
.nav{top:0;left:0;width:1200px;height:84px}
.nav a{color:var(--ink);text-decoration:none;font-size:15px}
.nav-left{left:112px;top:38px;display:flex;gap:30px}
.nav-left a.active{border-bottom:2px solid var(--ink);padding-bottom:4px}
.nav-right{left:686px;top:38px;display:flex;gap:30px}
.nav .btn{position:absolute;left:860px;top:28px;padding:10px 24px}
.brand{left:500px;top:18px;width:200px;text-align:center;display:flex;flex-direction:column;align-items:center;gap:5px}
.brand .dot{width:20px;height:20px;border-radius:50%;background:var(--ink)}
.brand span{font-weight:700;font-size:13px;letter-spacing:1px;text-transform:uppercase;line-height:1.25;color:var(--ink)}

/* hero */
.hero{left:80px;top:128px;width:1040px;height:592px;border-radius:24px;overflow:hidden;
  background:linear-gradient(180deg,#12243f 0%,#1f3d5c 30%,#8a5a3a 55%,#c97a3a 62%,#2e5d6a 72%,#1b3d44 100%)}
.hero h1{position:absolute;top:70px;width:100%;text-align:center;color:#fff;font-size:46px;line-height:1.2}
.hero .btn{position:absolute;left:444px;top:216px}

/* basecamp */
.basecamp h2{left:112px;top:820px;font-size:34px;line-height:1.3;width:420px}
.intro-note{left:630px;top:830px;width:460px;font-size:14px;line-height:1.55;color:var(--muted)}
.intro-card{left:112px;top:948px;width:488px;height:142px;background:var(--card);border-radius:14px;padding:22px 28px;font-size:13px;line-height:1.6;color:var(--muted);box-shadow:0 4px 14px rgba(0,0,0,.08)}
.intro-card p+p{margin-top:12px}
.intro-photo{left:630px;top:948px;width:460px;height:142px;background:linear-gradient(160deg,#b9c6d2,#8f9aa0 50%,#4e5b3c)}

/* suites */
.sec-title{left:112px;font-size:34px}
.sec-sub{left:112px;font-size:13px;color:var(--muted)}
.suite{top:1442px;width:310px;height:480px;background:var(--card);border-radius:16px;box-shadow:0 4px 14px rgba(0,0,0,.08);padding:20px}
.suite .pic{height:196px;border-radius:12px}
.suite h3{font-size:15px;font-weight:700;margin:22px 0 10px}
.suite p{font-size:12.5px;line-height:1.6;color:var(--muted)}
.suite .btn{position:absolute;left:28px;bottom:40px}

/* gallery */
.gallery .photo{position:absolute}
.more{left:508px;top:2920px}

/* reviews */
.reviews{left:80px;top:3036px;width:1040px;height:596px;border-radius:24px;overflow:hidden;
  background:linear-gradient(180deg,#2f3a44 0%,#4a5560 35%,#6b747a 55%,#25333d 100%)}
.reviews h2{position:absolute;left:32px;top:64px;color:#fff;font-size:34px}
.arrow{position:absolute;top:70px;width:32px;height:32px;border:2px solid #fff;border-radius:50%}
.review{top:3150px;height:380px;background:var(--card);border-radius:14px;padding:28px 30px;box-shadow:0 6px 18px rgba(0,0,0,.25);overflow:hidden}
.review.faded{opacity:.7}
.reviewer{display:flex;align-items:center;gap:14px}
.avatar{width:46px;height:46px;border-radius:50%;background:#9a9a9a}
.reviewer strong{display:block;font-size:16px}
.reviewer small{font-size:12px;color:var(--muted)}
.stars{display:flex;gap:4px;margin:22px 0 14px}
.review p{font-size:13px;line-height:1.6;color:var(--muted)}

/* book direct */
.book h2{left:112px;top:3756px;font-size:34px}
.book-copy{left:112px;top:3820px;width:440px;font-size:14px;line-height:1.6;color:var(--muted)}
.book-copy p+p{margin-top:14px}
.book .btn{position:absolute;left:112px;top:4018px}
.book-photo{left:600px;top:3724px;width:600px;height:380px;border-radius:20px 0 0 20px;background:linear-gradient(160deg,#d8cfc0,#b9ad99 45%,#6b5b48 75%,#3d3a36)}

/* footer */
.footer{left:40px;top:4140px;width:1120px;height:484px;background:var(--night);border-radius:24px;color:#fff;text-align:center}
.footer .brand{left:460px;top:50px}
.footer .brand .dot{background:#fff}
.footer .brand span{color:#fff;font-size:15px}
.tagline{position:absolute;top:224px;width:100%;font-size:17px;letter-spacing:1px}
.fline{position:absolute;left:200px;width:720px;height:1px;background:#555}
.fnav{position:absolute;top:300px;width:100%;display:flex;justify-content:center;gap:28px;font-size:13px}
.fnav a{color:#fff;text-decoration:none}
.copy{position:absolute;top:436px;width:100%;font-size:12px;color:#ccc}
</style>
</head>
<body>

<header class="nav abs">
  <nav class="nav-left abs">
    <a class="active" href="#">Home</a><a href="#">Suites</a><a href="#">Gallery</a><a href="#">Location</a><a href="#">Things To Do</a>
  </nav>
  <div class="brand abs"><i class="dot"></i><span>Tollen Ridge<br>Canvas Camps</span></div>
  <nav class="nav-right abs"><a href="#">Reviews</a><a href="#">Contact</a></nav>
  <a class="btn" href="#">Check Availability</a>
</header>

<section class="hero abs" role="img" aria-label="Mountain peaks at sunrise above a turquoise alpine lake">
  <h1>Stay Near the Beauty of Morvane<br>National Park</h1>
  <a class="btn" href="#">Check Availability</a>
</section>

<section class="basecamp">
  <h2 class="abs">Your Basecamp for the Canadian Rockies</h2>
  <p class="intro-note abs">This unique stay is a balance of camping and glamour - hence glamping! Your dome includes a FREE Morvane National Park Pass for your use during your stay! Each unit will contains luxurious sleeping quarters</p>
  <div class="intro-card abs">
    <p>Located within easy reach of hiking trails, wildlife viewing areas, scenic drives, and year-round outdoor activities, our suites offer the perfect balance of convenience and tranquility.</p>
    <p>Whether you're planning a romantic getaway, a family vacation, or a solo adventure, you'll find everything you need for a memorable stay.</p>
  </div>
  <div class="intro-photo photo abs" role="img" aria-label="White geodesic glamping dome on a wooden deck among trees"></div>
</section>

<section class="suites">
  <h2 class="sec-title abs" style="top:1300px">Our Suites</h2>
  <p class="sec-sub abs" style="top:1374px">Each suite is thoughtfully prepared to provide comfort, privacy, and modern amenities so you can focus on enjoying your trip.</p>

  <article class="suite abs" style="left:112px">
    <div class="pic" role="img" aria-label="Glamping dome with a deck beside the forest" style="background:linear-gradient(160deg,#9fb0b8,#c9c4b8 45%,#4f5d3a)"></div>
    <h3>Modern Mountain Suite</h3>
    <p>A bright and welcoming space designed for relaxation after a day outdoors. Enjoy comfortable sleeping arrangements, a fully equipped kitchenette, fast Wi-Fi, and easy self check-in.</p>
    <a class="btn" href="#">Book Now</a>
  </article>
  <article class="suite abs" style="left:445px">
    <div class="pic" role="img" aria-label="Dome interior with a bed and plaid blankets" style="background:linear-gradient(160deg,#e3ddd2,#b9ab94 50%,#7a3b33)"></div>
    <h3>Cozy Studio Retreat</h3>
    <p>A quiet and comfortable studio offering everything you need for a restful stay. Ideal for guests looking for simplicity, convenience, and a peaceful environment.</p>
    <a class="btn" href="#">Book Now</a>
  </article>
  <article class="suite abs" style="left:780px">
    <div class="pic" role="img" aria-label="Dome interior with seating and a small kitchen" style="background:linear-gradient(160deg,#d9d1c4,#a89985 50%,#5d4e40)"></div>
    <h3>Adventure Base Suite</h3>
    <p>Designed for travelers who plan to spend their days exploring the outdoors and their evenings relaxing in comfort. Clean, modern, and conveniently located.</p>
    <a class="btn" href="#">Book Now</a>
  </article>
</section>

<section class="gallery">
  <h2 class="sec-title abs" style="top:2012px">Photo Gallery</h2>
  <p class="sec-sub abs" style="top:2082px">Take a closer look at our accommodations, amenities, and the beautiful surroundings that make this stay special.</p>
  <div class="photo" role="img" aria-label="Washroom cabins by the trees" style="left:112px;top:2140px;width:234px;height:232px;background:linear-gradient(170deg,#a8c2dc,#cfd6d8 50%,#4a5e38)"></div>
  <div class="photo" role="img" aria-label="Dome seen through the forest" style="left:360px;top:2140px;width:240px;height:232px;background:linear-gradient(170deg,#8e9ba4,#c8c6bd 50%,#3e4a30)"></div>
  <div class="photo" role="img" aria-label="Dome bedroom with red plaid bedding" style="left:112px;top:2388px;width:488px;height:472px;background:linear-gradient(170deg,#e7e1d6,#c8bca8 45%,#8a3530 70%,#4f4038)"></div>
  <div class="photo" role="img" aria-label="Island of pines on a bright blue mountain lake" style="left:615px;top:2140px;width:476px;height:470px;background:linear-gradient(180deg,#3f7fd4 0%,#8fb5e0 30%,#5a7a6e 55%,#2d8fb8 70%,#1b5f88 100%)"></div>
  <div class="photo" role="img" aria-label="Bed with plaid pillows inside the dome" style="left:615px;top:2625px;width:233px;height:235px;background:linear-gradient(170deg,#e2dccf,#9d2f2c 60%,#4a3b33)"></div>
  <div class="photo" role="img" aria-label="Clean washroom with toilet" style="left:860px;top:2625px;width:231px;height:235px;background:linear-gradient(170deg,#eceae6,#c5c2bc 60%,#8b8883)"></div>
  <a class="btn abs more" href="#">View More Gallery</a>
</section>

<section class="reviews abs" role="img" aria-label="Mountain lake at dusk behind guest reviews">
  <h2>What Our Guests Say</h2>
  <svg class="arrow" style="left:820px" viewBox="0 0 32 32"><path d="M18 10l-6 6 6 6" fill="none" stroke="#fff" stroke-width="2"/></svg>
  <svg class="arrow" style="left:884px" viewBox="0 0 32 32"><path d="M14 10l6 6-6 6" fill="none" stroke="#fff" stroke-width="2"/></svg>
</section>

<article class="review faded abs" style="left:-240px;width:408px">
  <p style="margin-top:150px;text-align:right">quiet and cozy, we slept so well here and loved the mountain view</p>
</article>
<article class="review abs" style="left:192px;width:408px">
  <div class="reviewer"><i class="avatar"></i><div><strong>Marisol</strong><small>Harrowgate, Ontario</small></div></div>
  <div class="stars">
    <svg width="100" height="18" viewBox="0 0 100 18"><g fill="#e7a928"><path id="s" d="M9 1l2.4 5.2 5.6.6-4.2 3.8 1.2 5.6L9 13.4 4 16.2l1.2-5.6L1 6.8l5.6-.6z"/><use href="#s" x="20"/><use href="#s" x="40"/><use href="#s" x="60"/><use href="#s" x="80"/></g></svg>
  </div>
  <p>Fantastic stay. Loved the tour, we had a private bathroom and the hosts genuinely went beyond to make sure we had everything we needed. Clean little dome and the perfect welcoming base. Quiet, comfortable and relaxing. Would happily book again!</p>
</article>
<article class="review abs" style="left:620px;width:392px">
  <div class="reviewer"><i class="avatar"></i><div><strong>Delphine</strong><small>Harrowgate, Ontario</small></div></div>
  <div class="stars">
    <svg width="100" height="18" viewBox="0 0 100 18"><g fill="#e7a928"><use href="#s"/><use href="#s" x="20"/><use href="#s" x="40"/><use href="#s" x="60"/><use href="#s" x="80"/></g></svg>
  </div>
  <p>My mom and I had an amazing time glamping at the dome! We originally planned for one night, but ended up staying two. Sitting by the fire and stargazing were the highlights of our trip. The bed was comfy and hosts kind. Highly recommend!</p>
</article>
<article class="review faded abs" style="left:1032px;width:400px">
  <div class="reviewer"><i class="avatar"></i></div>
  <p style="margin-top:80px">Great spot close to the park, spotless and warm</p>
</article>

<section class="book">
  <h2 class="abs">Book Direct &amp; Save</h2>
  <div class="book-copy abs">
    <p>Reserve your stay using our secure booking system below. Direct bookings guarantee the best available rates, flexible communication, and a seamless experience from reservation to checkout.</p>
    <p>Whether you're planning a romantic getaway, a family vacation, or a solo adventure, you'll find everything you need for a memorable stay.</p>
  </div>
  <a class="btn" href="#">Book Now</a>
  <div class="book-photo abs" role="img" aria-label="Bright dome interior with table, chairs and kitchenette"></div>
</section>

<footer class="footer abs">
  <div class="brand abs" style="width:200px"><i class="dot"></i><span>Tollen Ridge<br>Canvas Camps</span></div>
  <p class="tagline">DIRECT BOOKING • SECURE RESERVATIONS</p>
  <i class="fline" style="top:276px"></i>
  <nav class="fnav"><a href="#">HOME</a><a href="#">SUITES</a><a href="#">GALLERY</a><a href="#">LOCATION</a><a href="#">BOOK NOW</a><a href="#">CONTACT</a></nav>
  <i class="fline" style="top:350px"></i>
  <p class="copy">© 2026 TOLLEN RIDGE CANVAS CAMPS</p>
</footer>

</body>
</html>
```